Direct to Consumer extended service contract business with a new disruptive business model needs a

We need a customized wordpress design for a company called 'Bright Harbor Assurance'.
We provide an innovative and unique service contract protection program direct to consumers. This program provides monthly coverage for all electronics purchased in the last 4 years and all electronics the consumer purchases in the future for a low monthly fee. The overall design should communicate a sense of legitimacy, ethics, and superior customer service and support (in an industry that has a huge PR issue to overcome).
Electronics is the first product group, other product groups with different price points to launch in the future..

Target Market(s)

All purchasers of electronic goods...all demographics

Industry/Entity Type

Electronics

Font styles to use
Sans Serif

Requirements
Must have
• Customer Testimonials
Industry News
Customer ratings
Blog posts
Call to action messaging
Like the functional elements and design of quillmesa.example (need to be better)
Nice to have
• Like to see video testimonials
Social network "whats trending related to electronics or service contract industry"
Easy way to register products for warranty

```html
<!DOCTYPE html>
<html lang="en">
<head>
<meta charset="utf-8">
<title>Bright Harbor Assurance</title>
<link href="https://fonts.googleapis.com/css2?family=Open+Sans:wght@400;600&family=Ubuntu:ital,wght@0,400;0,500;0,700;1,400&family=Arimo:wght@400;700&display=swap" rel="stylesheet">
<style>
  :root{
    --dark:#2a2a2a;
    --darker:#303030;
    --green:#27855a;
    --green-light:#3c9a6c;
    --slate:#42464b;
    --pale:#e4e7e7;
    --pale-2:#e9ecec;
    --ink:#222;
    --muted:#666;
    --white:#fff;
    --link-blue:#2b4fa0;
  }
  *{box-sizing:border-box;margin:0;padding:0}
  html,body{width:857px;height:1200px;overflow:hidden}
  body{position:relative;background:var(--white);font-family:"Arimo",Arial,sans-serif;color:var(--ink)}
  .abs{position:absolute}

  /* top bar */
  .topbar{left:0;top:0;width:857px;height:36px;background:var(--dark)}
  .brand{left:100px;top:5px;color:var(--white);font-family:"Open Sans",sans-serif;font-size:22px;font-weight:400;line-height:26px}
  .callus{right:32px;top:4px;color:var(--white);font-family:"Open Sans",sans-serif;font-size:14px;line-height:26px}
  .callus strong{font-size:19px;font-weight:400;margin-left:4px}

  /* hero */
  .hero-art{left:0;top:36px;width:857px;height:319px;background:radial-gradient(ellipse at 50% 50%,#dfe3e1 0%,#f6f7f6 35%,#ffffff 70%)}

  /* nav */
  .mainnav{left:0;top:355px;width:857px;height:39px;background:var(--green)}
  .mainnav ul{list-style:none;position:absolute;left:99px;top:6px;display:flex;gap:0}
  .mainnav li{font-size:10px;color:var(--white);text-transform:uppercase;height:27px;line-height:27px;padding:0 18px;border-radius:3px}
  .mainnav li.active{background:var(--green-light)}
  .social{right:102px;top:9px;display:flex;gap:5px}
  .social span{width:21px;height:21px;border-radius:50%;background:#c9d6cf;display:block}

  /* welcome */
  .welcome{left:0;top:394px;width:857px;height:308px;background:linear-gradient(90deg,#dfe2e2 0%,#e8eaea 55%,#eef0f0 100%)}
  .welcome-photo{left:444px;top:0;width:360px;height:308px;background:linear-gradient(180deg,#e9ecec 0%,#c9c3bf 45%,#2e2f33 75%,#1f2023 100%)}
  .welcome h1{left:100px;top:56px;font-family:"Ubuntu",sans-serif;font-size:23px;font-weight:700;color:var(--ink);text-transform:uppercase;letter-spacing:.2px}
  .welcome .lead{left:100px;top:92px;width:310px;font-size:10.5px;font-weight:700;line-height:14px;color:var(--ink)}
  .welcome .body{left:100px;top:126px;width:330px;font-size:9px;line-height:13px;color:var(--muted)}
  .btn-more{left:99px;top:206px;width:57px;height:29px;border-radius:4px;background:var(--green);color:var(--white);font-size:10px;line-height:29px;text-align:center}

  /* features */
  .features{left:0;top:702px;width:857px;height:194px;background:var(--slate);border-top:3px solid #34373b}
  .feature{top:0;width:140px;height:194px;text-align:center}
  .feature h2{position:absolute;left:0;width:140px;top:43px;font-family:"Ubuntu",sans-serif;font-weight:500;font-size:18.5px;line-height:24px;color:var(--white)}
  .feature .rule{position:absolute;left:0;top:96px;width:140px;height:1px;background:#5c6166}
  .feature p{position:absolute;left:10px;width:120px;top:106px;font-size:7.5px;line-height:9.5px;color:#e6e6e6;font-weight:700}
  .feature .go{position:absolute;left:59px;top:148px;width:22px;height:22px;border-radius:50%;background:#2b2e31}

  /* content */
  .content{left:0;top:896px;width:857px;height:204px;background:var(--pale)}
  .content h3{font-family:"Ubuntu",sans-serif;font-weight:500;font-size:13px;color:var(--ink)}
  .post-thumb{width:48px;height:48px;border:1px solid #d0d3d3;background:linear-gradient(135deg,#f3d9c2,#e8b48f);padding:3px}
  .post-title{font-size:8.5px;font-weight:700;color:var(--ink)}
  .post-date{font-size:6.5px;font-weight:700;color:#888;text-transform:uppercase}
  .news-icon{width:13px;height:13px;border-radius:50%;background:#333}
  .news-title{font-size:8px;font-weight:700;color:var(--ink)}
  .news-body{left:337px;top:92px;width:240px;font-size:7.5px;line-height:11.5px;color:#777}
  .news-rule{left:337px;top:143px;width:240px;height:1px;background:#cfd2d2}
  .quote-box{left:606px;top:49px;width:156px;height:78px;background:var(--pale-2);border:1px solid #dadddd;padding:8px 10px}
  .quote-box p{font-family:"Ubuntu",sans-serif;font-style:italic;font-size:8.5px;line-height:12px;color:#555}
  .avatar{left:612px;top:143px;width:36px;height:38px;background:linear-gradient(180deg,#c8d3db,#8c9aa4)}
  .author{left:660px;top:146px;font-family:"Ubuntu",sans-serif;font-style:italic;font-size:10px;color:var(--link-blue)}
  .author-place{left:660px;top:161px;font-family:"Ubuntu",sans-serif;font-style:italic;font-size:8px;color:#444}

  /* footer */
  .footnav{left:0;top:1100px;width:857px;height:52px;background:var(--dark)}
  .footnav ul{list-style:none;display:flex;justify-content:center;padding-top:20px}
  .footnav li{font-size:9.5px;color:#ddd}
  .footnav li.sep{padding:0 15px;color:#aaa}
  .copyright{left:0;top:1152px;width:857px;height:48px;background:var(--darker);color:#777;font-size:8.5px;text-align:center;padding-top:10px}
</style>
</head>
<body>

<header class="abs topbar">
  <div class="abs brand">Bright Harbor Assurance</div>
  <div class="abs callus">Call us now <strong>1 800 555 0142</strong></div>
</header>

<section class="abs hero-art" role="img" aria-label="Hand-lettered headline about taking your phone in for diagnosis, with a cracked smartphone circled in green and sketched nuts and bolts"></section>

<nav class="abs mainnav">
  <ul>
    <li class="active">Home</li>
    <li>Reviews</li>
    <li>Services</li>
    <li>Blog</li>
    <li>Contacts</li>
  </ul>
  <div class="abs social" aria-label="Social links">
    <span></span><span></span><span></span><span></span>
  </div>
</nav>

<section class="abs welcome">
  <div class="abs welcome-photo" role="img" aria-label="Smiling customer service representative in a dark suit"></div>
  <h1 class="abs">Welcome to our website!</h1>
  <p class="abs lead">Lorem ipsum dolor sit amet conse ctetur adipisicing elit&nbsp; sed do eiusmod tempor incidi</p>
  <p class="abs body">Phasellus porta. Fusce susct varius mi. Cum sociis natoque penatibus et magnis dis parturient montes, nascetur ridiculus mus. Nulla dui. Fusce feugiat malesuada odio. Arenean lorem ipsum dolor sit amet conse ctetur adipisicing elit, sed do eiusmod tempor incidi dunt ut labore et dolore magna aliqua. Ut enim ad minim veniam....</p>
  <div class="abs btn-more">More</div>
</section>

<section class="abs features">
  <div class="abs feature" style="left:122px">
    <h2>Monthly<br>Coverage</h2><div class="rule"></div>
    <p>Et harum quidem rerum harum quidem rerum facilis consequtur out</p>
    <svg class="go" viewBox="0 0 22 22"><path d="M9.5 7l4 4-4 4" fill="none" stroke="#fff" stroke-width="2"/></svg>
  </div>
  <div class="abs feature" style="left:278px">
    <h2>Unique<br>Services</h2><div class="rule"></div>
    <p>Et harum quidem rerum harum quidem rerum facilis consequtur out</p>
    <svg class="go" viewBox="0 0 22 22"><path d="M9.5 7l4 4-4 4" fill="none" stroke="#fff" stroke-width="2"/></svg>
  </div>
  <div class="abs feature" style="left:432px">
    <h2>Inspection &amp;<br>Testing</h2><div class="rule"></div>
    <p>Et harum quidem rerum harum quidem rerum facilis consequtur out</p>
    <svg class="go" viewBox="0 0 22 22"><path d="M9.5 7l4 4-4 4" fill="none" stroke="#fff" stroke-width="2"/></svg>
  </div>
  <div class="abs feature" style="left:586px">
    <h2>New<br>Technologies</h2><div class="rule"></div>
    <p>Et harum quidem rerum harum quidem rerum facilis consequtur out</p>
    <svg class="go" viewBox="0 0 22 22"><path d="M9.5 7l4 4-4 4" fill="none" stroke="#fff" stroke-width="2"/></svg>
  </div>
</section>

<section class="abs content">
  <h3 class="abs" style="left:106px;top:22px">Latest Posts</h3>
  <div class="abs post-thumb" style="left:106px;top:54px" role="img" aria-label="Post thumbnail photo"></div>
  <div class="abs post-title" style="left:168px;top:64px">Dipisicing elit sed do eiusmod</div>
  <div class="abs post-date" style="left:168px;top:78px">March 14, 2013</div>
  <div class="abs post-thumb" style="left:106px;top:113px" role="img" aria-label="Post thumbnail photo"></div>
  <div class="abs post-title" style="left:168px;top:123px">Dipisicing elit sed do eiusmod</div>
  <div class="abs post-date" style="left:168px;top:137px">March 14, 2013</div>

  <h3 class="abs" style="left:337px;top:22px">News</h3>
  <svg class="abs news-icon" style="left:337px;top:58px" viewBox="0 0 13 13"><path d="M3.5 6.5h6" stroke="#fff" stroke-width="1.6"/></svg>
  <div class="abs news-title" style="left:358px;top:59px">Quisque nulla</div>
  <p class="abs news-body">Phasellus porta. Fusce susct varius mi. Cum sociis natoque penatibus et magnis dis parturient montes, nascetur ridiculus mus. Nulla dui massa dolore sed lorem.</p>
  <div class="abs news-rule"></div>
  <svg class="abs news-icon" style="left:337px;top:156px" viewBox="0 0 13 13"><path d="M3.5 6.5h6M6.5 3.5v6" stroke="#fff" stroke-width="1.6"/></svg>
  <div class="abs news-title" style="left:358px;top:157px">Vestibulum iaculis</div>

  <h3 class="abs" style="left:611px;top:20px">Testimonials</h3>
  <div class="abs quote-box"><p>"Aenean nonummy hendrerit mau Fusce suscipit varius mi sed. Cum penatibus et magnis dis parturient nascetur ridiculus mus. Nulla dui....</p></div>
  <div class="abs avatar" role="img" aria-label="Customer portrait"></div>
  <div class="abs author">Dana Whitcombe</div>
  <div class="abs author-place">USA. Detroit</div>
</section>

<footer>
  <nav class="abs footnav">
    <ul>
      <li>Home</li><li class="sep">|</li>
      <li>Reviews</li><li class="sep">|</li>
      <li>Services</li><li class="sep">|</li>
      <li>Blog</li><li class="sep">|</li>
      <li>Contacts</li>
    </ul>
  </nav>
  <div class="abs copyright">Copyright 2014 www.brightharbor.example All Rights Reserved.</div>
</footer>

</body>
</html>
```